Business card for my new company (Accounting firm)

I need a business card for my new business Brightwell Advisory and Ledger SA. Our services are accounting, tax, audit and financial management. Our customers are small companies, start-ups and new companies. The final design has to show financial security, trust and growth. Please find our logo attached to the business card. Text for the business card: Brightwell Advisory and Ledger SA Tomas Varenholt Director and Founder Certified Accountant Tel. 022 418 57 34 tv@clairevalconseil.ch www.clairevalconseil.ch Rue des Vergières 27 1201 Geneva
Target Market(s)
Our customers are small companies, start-ups and new companies.
Industry/Entity Type
Finance And Accounting
Contact Information for Business Card
Claireval Conseil et Comptes SA
Tomas Varenholt
Directeur et Fondateur
Expert-comptable diplômé
Tél. 022 418 57 34
tv@clairevalconseil.ch
www.clairevalconseil.ch
Rue des Vergières 27
1201 Genève

```html
<!DOCTYPE html>
<html lang="fr">
<head>
<meta charset="utf-8">
<title>Claireval Conseil et Comptes – Carte de visite</title>
<link href="https://fonts.googleapis.com/css2?family=Roboto:wght@400;500;700&display=swap" rel="stylesheet">
<style>
  :root {
    --backdrop: #e4e5e7;
    --blue-light: #2ea3da;
    --blue-deep: #1b6a9c;
    --blue-name: #1f5f98;
    --ink: #3a3a3c;
    --ink-soft: #55575a;
    --paper: #f7f7f7;
  }
  * { margin: 0; padding: 0; box-sizing: border-box; }
  html, body { width: 1200px; height: 726px; overflow: hidden; }
  body {
    background: var(--backdrop);
    font-family: "Roboto", Arial, sans-serif;
    position: relative;
  }
  .card {
    position: absolute;
    top: 213px;
    width: 520px;
    height: 300px;
    border-radius: 4px;
    overflow: hidden;
    box-shadow: 0 10px 28px rgba(0,0,0,.12);
  }
  /* Front */
  .card-front {
    left: 50px;
    background: linear-gradient(160deg, var(--blue-light) 0%, var(--blue-deep) 100%);
    color: #fff;
    text-align: center;
  }
  .front-brand {
    position: absolute;
    top: 98px; left: 0; right: 0;
  }
  .brand-name {
    font-weight: 500;
    font-size: 44px;
    letter-spacing: 6px;
    line-height: 1;
  }
  .brand-line {
    font-weight: 500;
    font-size: 13px;
    letter-spacing: 5.5px;
    margin-top: 8px;
  }
  .front-web {
    position: absolute;
    bottom: 42px; left: 0; right: 0;
    font-size: 14px;
    font-weight: 500;
    letter-spacing: .3px;
  }
  /* Back */
  .card-back {
    left: 630px;
    background: var(--paper);
    color: var(--ink-soft);
  }
  .back-band {
    position: absolute;
    left: 0; right: 0; bottom: 0;
    height: 8px;
    background: linear-gradient(90deg, var(--blue-light), var(--blue-deep));
  }
  .back-brand {
    position: absolute;
    top: 44px; right: 34px;
    color: var(--ink);
    text-align: left;
    display: flex;
    align-items: center;
    gap: 10px;
  }
  .brand-mark {
    width: 14px; height: 14px;
    background: var(--blue-light);
  }
  .back-brand .brand-name { font-size: 30px; letter-spacing: 3px; font-weight: 500; }
  .back-brand .brand-line { font-size: 9px; letter-spacing: 3.6px; margin-top: 5px; font-weight: 500; }
  .back-web-top {
    position: absolute;
    top: 118px; right: 34px;
    font-size: 12px;
    color: var(--ink);
    display: flex; align-items: center; gap: 5px;
  }
  .person {
    position: absolute;
    left: 34px; top: 150px;
  }
  .person-name {
    color: var(--blue-name);
    font-weight: 700;
    font-size: 19px;
    margin-bottom: 4px;
  }
  .person-role { font-size: 11.5px; line-height: 1.35; color: var(--ink-soft); }
  .contacts {
    position: absolute;
    left: 34px; top: 232px;
    font-size: 12px;
    color: var(--ink);
    line-height: 1.6;
  }
  .contact-row { display: flex; align-items: center; gap: 6px; }
  .contact-row .gap { width: 10px; }
  .icon { width: 11px; height: 11px; fill: var(--blue-name); flex: none; }
</style>
</head>
<body>
  <section class="card card-front" aria-label="Recto">
    <div class="front-brand">
      <div class="brand-name">CLAIREVAL</div>
      <div class="brand-line">CONSEIL ET COMPTES</div>
    </div>
    <div class="front-web">www.clairevalconseil.ch</div>
  </section>

  <section class="card card-back" aria-label="Verso">
    <div class="back-brand">
      <span class="brand-mark"></span>
      <div>
        <div class="brand-name">CLAIREVAL</div>
        <div class="brand-line">CONSEIL ET COMPTES</div>
      </div>
    </div>

    <div class="person">
      <div class="person-name">Tomas Varenholt</div>
      <div class="person-role">Directeur et Fondateur<br>Expert-comptable diplômé</div>
    </div>

    <div class="contacts">
      <div class="contact-row">
        <svg class="icon" viewBox="0 0 24 24"><path d="M6.6 10.8a15 15 0 0 0 6.6 6.6l2.2-2.2a1 1 0 0 1 1-.25 11.4 11.4 0 0 0 3.6.57 1 1 0 0 1 1 1V20a1 1 0 0 1-1 1A17 17 0 0 1 3 4a1 1 0 0 1 1-1h3.5a1 1 0 0 1 1 1c0 1.25.2 2.45.57 3.6a1 1 0 0 1-.25 1z"/></svg>
        <span>022 418 57 34</span>
        <span class="gap"></span>
        <svg class="icon" viewBox="0 0 24 24"><path d="M2 5h20v14H2z M2 5l10 8 10-8" fill="none" stroke="#1f5f98" stroke-width="2.4"/></svg>
        <span>tv@clairevalconseil.ch</span>
        <span class="gap"></span>
        <svg class="icon" viewBox="0 0 24 24"><circle cx="12" cy="12" r="10" fill="none" stroke="#1f5f98" stroke-width="2.2"/><path d="M2 12h20M12 2c3 3 3 17 0 20M12 2c-3 3-3 17 0 20" fill="none" stroke="#1f5f98" stroke-width="1.8"/></svg>
        <span>www.clairevalconseil.ch</span>
      </div>
      <div class="contact-row">
        <svg class="icon" viewBox="0 0 24 24"><path d="M12 2a7 7 0 0 0-7 7c0 5 7 13 7 13s7-8 7-13a7 7 0 0 0-7-7zm0 9.5A2.5 2.5 0 1 1 12 6.5a2.5 2.5 0 0 1 0 5z"/></svg>
        <span>Rue des Vergières 27 1201 Genève</span>
      </div>
    </div>

    <div class="back-band"></div>
  </section>
</body>
</html>
```